Wine Label Design-Hollow Creek Vineyard

Hollow Creek Vineyard is in the Barossa Valley in South Australia. The Barossa is recognized as Australia's premier wine region, producing Australia's icon wines and some " new takes on traditional".
This family owned and operated vineyard grows some exceptionally high quality fruit. Most of the fruit is sold and used for some of Australia's most iconic wines. Small quantities are retained by the owners for some wines with very limited availability. (Wines were previously sold as Brackwell Vineyards Hollow Creek ( Shiraz, Cabernet etc).

The wines will in the future be labeled simply ‘Hollow Creek Vineyard’. The label will launch this new identity for the single family single vineyard and its high quality wines which are a true expression of the vineyard and derive from the Hollow Creek common to this ancient area (800-2000 million years old).
The label should reflect
• Single vineyard, family owned
• vines in very old rock & soils
• High quality & reliability
• Edgy but true, design based thinking (Please note:blue is generally seen as an unacceptable colour for a wine label?? Don’t ask me why)

The wines will be sold mostly direct in Australia ( ie not through retail stores), with limited export to Asia, Scandinavia and Canada.
There are three quality levels and price points in the portfolio
1. Entry level premium for everyday drinking for discriminating drinkers-approx AUD20
2. Super Premium-approx AUD30
3. Limited Release ultlra premium-AUD75-90?
We envisage three variations on the label but with an obvious & common design element. This design element should be able to be used for corporate identification and promotion
The paper stock will be waterproof and self adhesive. Our preference is for designs that engage the user by appealing to both sight and touch. It is preferred that textures be added eg embossing, high build varnish etc-rather than be a facet of the stock itself.
For information on statutory label requirements refer to www.vintnerregistry-example.com . In brief
o Front label need not show any mandatory information. However we would prefer Variety, Barossa Valley, Year and alcohol to be shown on the front label
o Back label should show all mandatories and allow for a bar code
Updates

Project Deadline Extended
Reason: I've had a problem with my wireless broadband account and reception has been intermittent to say the least to the extent that I switched off at the weekend. Just going downtown now for a 'polite discussion' with my service provider.

Project Deadline Extended
Reason: I have receiver insufficient designs of quality which we would consider. Too many designs have a "cut and paste" appearance - too few exhibit an original art/design element which truly identifies the product.

Gals & Guys

most of the designs submitted lack punch and originality and are totally unmemorable.
Please-get on Searcho or whatever enter "Wine Label Designs" and do some research b4 u waste your time and mine. Formulaic cut and paste will not win the day. That's not to say that cut and paste can't work-but it must have some originality, impact and command attention. Please surprise me.

Following on from a question from a designer about who is our competition and what we are looking for I sent the following 
"I don't think I can add anything new. Read the brief and comments again and research wine labels on the web. In 30 minutes you'll get a good idea of the creative edgy designs in the industry. There are a plethora of collections. Our competition-anyone with a label. In 2010 there were over 2400 "producers" in other words 2400 producers with at least one label. In fact there are over 25000 Australian wines and then the numerous imported wines.

Target Market(s)

$20 people who budget everyday but have graduated from drinking 'entry level' wines. These people will likely fit into Cat. (b) in the $30 wine

$30 (a) will not over-compromise on some everyday discretionary expenditure.(b) might buy for special occasions

$70-$90 Professional/successful people with high disposable/discretionary income not particularly worried about recession. wine geeks.

Industry/Entity Type

Retail

Requirements
Must have
• identifiable element across range of wines

```html
<!DOCTYPE html>
<html lang="en">
<head>
<meta charset="utf-8">
<title>Hollow Creek Vineyard – Front Label</title>
<link rel="stylesheet" href="https://fonts.googleapis.com/css2?family=Libre+Baskerville:wght@400&family=Crimson+Text&display=swap">
<style>
  :root {
    --page-bg: #e6e7e9;
    --paper-white: #ffffff;
    --silver-dark: #9d9d9f;
    --silver-mid: #c9c9cb;
    --silver-light: #f3f3f4;
    --ink: #141414;
    --ornament-dark: #4a4a4c;
    --ornament-light: #b8b8ba;
  }
  * { margin: 0; padding: 0; box-sizing: border-box; }
  html, body {
    width: 1200px;
    height: 1200px;
    overflow: hidden;
    background: var(--page-bg);
  }
  .canvas {
    position: relative;
    width: 1200px;
    height: 1200px;
    display: flex;
    align-items: center;
    justify-content: center;
  }
  .front-label {
    position: relative;
    width: 1040px;
    height: 640px;
    filter: drop-shadow(0 4px 10px rgba(0,0,0,0.12));
  }
  .label-paper {
    position: absolute;
    inset: 0;
    width: 100%;
    height: 100%;
  }
  .label-content {
    position: absolute;
    inset: 0;
    color: var(--ink);
    text-align: center;
  }
  .wordmark {
    position: absolute;
    top: 100px;
    left: 0;
    right: 0;
    font-family: "Libre Baskerville", "Times New Roman", serif;
    font-weight: 400;
    font-size: 58px;
    line-height: 1;
    letter-spacing: 1px;
    white-space: nowrap;
  }
  .region {
    position: absolute;
    top: 222px;
    left: 0;
    right: 0;
    font-family: "Libre Baskerville", "Times New Roman", serif;
    font-size: 40px;
    letter-spacing: 3px;
    line-height: 1;
  }
  .ornament {
    position: absolute;
    top: 290px;
    left: 230px;
    width: 580px;
    height: 115px;
    border-radius: 50% / 40%;
    background: radial-gradient(ellipse at center, var(--ornament-dark) 0%, var(--ornament-light) 55%, rgba(184,184,186,0) 72%);
    opacity: 0.8;
  }
  .vintage {
    position: absolute;
    top: 530px;
    left: 0;
    right: 0;
    font-family: "Crimson Text", "Times New Roman", serif;
    font-size: 40px;
    line-height: 1;
  }
  .alcohol {
    position: absolute;
    top: 572px;
    right: 40px;
    font-family: "Crimson Text", "Times New Roman", serif;
    font-size: 19px;
    line-height: 1;
  }
</style>
</head>
<body>
<main class="canvas">
  <section class="front-label" aria-label="Hollow Creek Vineyard front label">
    <svg class="label-paper" viewBox="0 0 1040 640" aria-hidden="true">
      <defs>
        <linearGradient id="silver-foil" x1="0" y1="0" x2="1" y2="0.3">
          <stop offset="0" stop-color="#9d9d9f"/>
          <stop offset="0.35" stop-color="#c9c9cb"/>
          <stop offset="0.68" stop-color="#f3f3f4"/>
          <stop offset="1" stop-color="#c9c9cb"/>
        </linearGradient>
      </defs>
      <path class="torn-edge" fill="#ffffff"
        d="M4 6 L60 2 L118 7 L170 1 L235 6 L290 2 L350 8 L410 3 L470 7 L530 1 L590 6 L650 2 L710 8 L770 3 L830 6 L890 1 L950 7 L1000 2 L1036 5
           L1039 60 L1034 120 L1040 180 L1035 240 L1039 300 L1033 360 L1040 420 L1035 480 L1039 540 L1034 600 L1037 636
           L980 638 L920 633 L860 639 L800 634 L740 638 L680 632 L620 639 L560 634 L500 638 L440 633 L380 639 L320 634 L260 638 L200 633 L140 639 L80 634 L3 637
           L6 580 L1 520 L7 460 L2 400 L6 340 L1 280 L7 220 L2 160 L6 100 L1 50 Z"/>
      <path class="silver-field" fill="url(#silver-foil)"
        d="M20 22 L48 16 L75 24 L102 17 L130 25 L160 18 L190 23 L222 15 L250 24 L282 18 L310 25 L345 16 L375 23 L405 17 L440 24 L470 15 L500 22 L535 17 L565 25 L600 16 L630 23 L662 18 L695 25 L725 16 L758 22 L790 17 L820 24 L852 15 L885 23 L915 18 L948 25 L980 17 L1022 22
           L1017 55 L1025 90 L1016 125 L1024 160 L1017 195 L1025 230 L1015 265 L1023 300 L1016 335 L1025 370 L1017 405 L1024 440 L1015 475 L1023 510 L1017 545 L1025 580 L1020 620
           L985 624 L952 616 L920 625 L888 617 L855 623 L822 615 L790 624 L758 617 L725 625 L692 616 L660 623 L628 615 L595 624 L562 617 L530 625 L498 616 L465 623 L432 615 L400 624 L368 617 L335 625 L302 616 L270 623 L238 615 L205 624 L172 617 L140 625 L108 616 L75 623 L44 616 L18 622
           L24 585 L15 550 L23 515 L16 480 L25 445 L17 410 L24 375 L15 340 L23 305 L16 270 L25 235 L17 200 L24 165 L15 130 L23 95 L16 60 Z"/>
    </svg>
    <div class="label-content">
      <h1 class="wordmark">Hollow Creek Vineyard</h1>
      <p class="region">BAROSSA VALLEY</p>
      <div class="ornament" role="img" aria-label="Symmetrical engraved flourish ornament beneath the region name"></div>
      <p class="vintage">Vintage 2012</p>
      <p class="alcohol">13.5% AlcVol</p>
    </div>
  </section>
</main>
</body>
</html>
```